biopharma company with breakthrough technology needs new web design

The rise of multidrug resistant bacteria pose a worldwide healthcare crisis as new bacterial strains are now resistant to nearly all existing antibiotics. Q4 Biotic is developing a class of new compounds known as ceragenins that have broad spectrum activity against even resistant strains. Our website needs a facelift. See www.q4biotic.com. We want to provide more information on the landing page and make it more visually appealing. see for example: http://vorelaxin.com/#sthash.KmpwRtaZ.qxle
Industry/Entity Type
Healthcare

```html
<!DOCTYPE html>
<html lang="en">
<head>
<meta charset="utf-8">
<title>Q4 Biotic</title>
<link href="https://fonts.googleapis.com/css2?family=Montserrat:wght@300;400;500;600&family=Arimo:ital,wght@0,400;0,700;1,400&display=swap" rel="stylesheet">
<style>
:root{
  --navy:#0b1f63;
  --cyan:#1eb0e8;
  --ink:#1c1c1c;
  --text:#5a5a5a;
  --icon:#8a8a8a;
  --rule:#d6d6d6;
  --page:#f4f4f4;
}
*{margin:0;padding:0;box-sizing:border-box}
html,body{width:813px;height:1200px;overflow:hidden;background:var(--page)}
body{position:relative;font-family:"Arimo",Arial,sans-serif;color:var(--text)}
.abs{position:absolute}
.brand{left:52px;top:22px;display:flex;align-items:center;gap:8px;font-family:"Montserrat",sans-serif;font-weight:600;font-size:26px;color:var(--navy);letter-spacing:.5px}
.brand-mark{width:18px;height:18px;background:var(--cyan)}
.nav{top:35px;left:0;width:813px;height:16px;font-family:"Montserrat",sans-serif;font-size:11.5px;color:var(--ink)}
.nav a{position:absolute;text-decoration:none;color:inherit;letter-spacing:.3px}
.nav a.active{color:var(--cyan)}
.hero{left:52px;top:85px;width:708px;height:373px;
  background:radial-gradient(ellipse 55% 70% at 72% 55%,#b3474f 0%,#8f5766 30%,#8ea1bd 65%,#c9d5e3 100%);
  box-shadow:0 6px 6px -4px rgba(0,0,0,.35)}
.dot{top:425px;width:9px;height:9px;border-radius:50%;border:1.5px solid #fff}
.dot.on{background:#fff}
.headline{top:490px;left:0;width:813px;text-align:center;font-family:"Montserrat",sans-serif;font-weight:300;font-size:21px;line-height:28px;color:var(--ink);letter-spacing:.3px}
.headline b{font-weight:500}
.headline .accent{color:var(--navy)}
.intro{top:556px;left:123px;width:567px;text-align:center;font-size:10px;line-height:15.6px}
.btn{left:354px;top:663px;width:105px;height:35px;background:var(--navy);color:#fff;font-size:11.5px;display:flex;align-items:center;justify-content:center;border-radius:2px;letter-spacing:.2px}
.card-img{top:734px;width:338px;height:125px}
.card-img.molecule{left:52px;background:radial-gradient(ellipse 80% 90% at 65% 50%,#8fd3f5 0%,#3fa3dc 45%,#1d6fb3 100%)}
.card-img.device{left:422px;height:127px;background:radial-gradient(ellipse 75% 80% at 50% 55%,#6f9c95 0%,#3c7f74 55%,#2a6459 100%)}
.card{top:874px;width:345px;text-align:center}
.card h2{font-family:"Montserrat",sans-serif;font-weight:400;font-size:21px;color:var(--ink);letter-spacing:.5px;margin-bottom:9px}
.card p{font-size:10px;line-height:15.6px;height:48px}
.card .more{display:block;margin-top:13px;font-size:11.5px}
.rule{left:52px;width:708px;height:1px;background:var(--rule)}
.foot-h{top:1037px;font-family:"Montserrat",sans-serif;font-weight:400;font-size:12px;color:var(--navy);letter-spacing:.6px}
.foot-h.strong{font-weight:500}
.support{left:69px;top:1064px;font-size:10px;line-height:15.6px;font-style:normal}
.support .name{font-size:12.5px;color:var(--navy);line-height:18px}
.support b{font-weight:700}
.legal{left:241px;top:1064px;font-size:10px;line-height:21px}
.legal .link{color:var(--cyan)}
.news{left:413px;width:150px;height:38px}
.news .thumb{position:absolute;left:0;top:0;width:35px;height:35px;border-radius:50%}
.news .copy{position:absolute;left:42px;top:-3px;font-size:10px;line-height:14px}
.news .date{font-style:italic;font-size:8px;color:var(--cyan);display:block;line-height:11px;padding-left:1px}
.social{top:1064px;width:14px;height:14px}
.social svg{width:14px;height:14px;display:block}
.copyright{top:1175px;left:0;width:813px;text-align:center;font-family:"Montserrat",sans-serif;font-size:10px;color:#555}
.copyright .co{color:var(--cyan)}
</style>
</head>
<body>

<div class="abs brand"><span class="brand-mark"></span>Q4 Biotic</div>

<nav class="abs nav">
  <a class="active" style="left:276px">HOME</a>
  <a style="left:338px">ABOUT</a>
  <a style="left:404px">TECHNOLOGY</a>
  <a style="left:510px">MEDICAL DEVICES</a>
  <a style="left:642px">NEWS</a>
  <a style="left:702px">CONTACT</a>
</nav>

<div class="abs hero" role="img" aria-label="Laboratory scene with a researcher pipetting red liquid beside a microscope and sample tubes"></div>
<span class="abs dot on" style="left:381px"></span>
<span class="abs dot" style="left:402px"></span>
<span class="abs dot" style="left:423px"></span>

<h1 class="abs headline">FORTIFYING <b>MEDICAL DEVICES</b> WITH THEIR OWN IMMUNE<br>SYSTEMS TO PREVENT <span class="accent">HOSPITAL-ACQUIRED</span> <b>INFECTIONS</b></h1>

<p class="abs intro">Q4 Biotic is a development-stage medical device company focused upon commercializing antimicrobial medical devices and coatings to address the multibillion dollar public health and economic burden associated with medical device-related hospital acquired infections (“HAIs”). Q4 Biotic’s business is based on the application of a novel, proprietary class of compounds known as ceragenins or CSAs (“ceragenins” or “CSAs”) to medical devices for the purpose of transforming existing medical devices into high value devices with antimicrobial, anti-inflammatory and other therapeutic properties that improve patient outcomes and lower the overall cost of care.</p>

<div class="abs btn">READ MORE</div>

<div class="abs card-img molecule" role="img" aria-label="Blue molecular structure illustration"></div>
<div class="abs card-img device" role="img" aria-label="Medical tubing, syringe and tape on green surgical cloth"></div>

<section class="abs card" style="left:49px">
  <h2>CERAGENINS</h2>
  <p>Ceragenins, also known as cationic steroidal antimicrobials or CSAs, are synthetic, non-peptide small molecule mimetics of endogenous host defense or antimicrobial peptides.</p>
  <span class="more" style="color:var(--navy)">READ MORE</span>
</section>
<section class="abs card" style="left:419px">
  <h2>MEDICAL DEVICES</h2>
  <p>Infections are a leading cause of death and illness worldwide. With the rapid rise of drug-resistant bacteria, nearly 70 percent of infections in the U.S. are now drug resistant.</p>
  <span class="more" style="color:var(--ink)">READ MORE</span>
</section>

<div class="abs rule" style="top:1016px"></div>

<h3 class="abs foot-h" style="left:69px">SUPPORT</h3>
<h3 class="abs foot-h" style="left:241px">LEGAL</h3>
<h3 class="abs foot-h" style="left:413px">LATEST NEWS</h3>
<h3 class="abs foot-h strong" style="left:592px">STAY CONNECTED</h3>

<address class="abs support">
  <div class="name">Q4 Biotic</div>
  1420 Harlow Ave Dayton,<br>OH 45402<br>
  <b>Call</b> : 877-555-0142<br>
  <b>Fax</b> : 877-555-0143
</address>

<div class="abs legal">
  <div class="link">Privacy Policy</div>
  <div>Terms &amp; Conditions</div>
</div>

<div class="abs news" style="top:1067px">
  <div class="thumb" role="img" aria-label="News thumbnail, laboratory" style="background:radial-gradient(circle,#ece6e4,#b9a9a6)"></div>
  <div class="copy">Lorem Ipsum is simply<br>dummy text of the.<span class="date">12th June, 2016</span></div>
</div>
<div class="abs news" style="top:1117px">
  <div class="thumb" role="img" aria-label="News thumbnail, blue bacteria" style="background:radial-gradient(circle,#6cc6f2,#1572c0)"></div>
  <div class="copy">Lorem Ipsum is simply<br>dummy text of the.<span class="date">12th June, 2016</span></div>
</div>

<a class="abs social" style="left:588px" aria-label="Email">
  <svg viewBox="0 0 14 14"><rect x="1" y="3" width="12" height="8.5" rx="1" fill="none" stroke="var(--cyan)" stroke-width="1.4"/><path d="M1.5 3.8 7 8l5.5-4.2" fill="none" stroke="var(--cyan)" stroke-width="1.4"/></svg>
</a>
<a class="abs social" style="left:616px" aria-label="Chat">
  <svg viewBox="0 0 14 14"><path d="M2 2.5h10a1 1 0 0 1 1 1v5.5a1 1 0 0 1-1 1H6l-3 2.5V10H2a1 1 0 0 1-1-1V3.5a1 1 0 0 1 1-1z" fill="var(--icon)"/></svg>
</a>
<a class="abs social" style="left:646px" aria-label="Share">
  <svg viewBox="0 0 14 14"><circle cx="3" cy="7" r="2" fill="var(--icon)"/><circle cx="11" cy="3" r="2" fill="var(--icon)"/><circle cx="11" cy="11" r="2" fill="var(--icon)"/><path d="M3 7 11 3M3 7l8 4" stroke="var(--icon)" stroke-width="1.3"/></svg>
</a>
<a class="abs social" style="left:676px" aria-label="Website">
  <svg viewBox="0 0 14 14"><circle cx="7" cy="7" r="5.8" fill="none" stroke="var(--icon)" stroke-width="1.3"/><ellipse cx="7" cy="7" rx="2.5" ry="5.8" fill="none" stroke="var(--icon)" stroke-width="1.1"/><path d="M1.2 7h11.6" stroke="var(--icon)" stroke-width="1.1"/></svg>
</a>

<div class="abs rule" style="top:1165px"></div>
<p class="abs copyright">© <span class="co">Q4 BIOTIC</span> - 2016. All Rights Reserved.</p>

</body>
</html>
```